New Business Card Design for Manufacturing

We are an engineering/manufacturing company that offers Advanced machining/assembly/engineering services, as well as innovative products for the heavy duty engine cooling markets.

We are looking to get a new business card designed that is clean and modern looking, but still fits the wide range of technical/skilled work we do.

- We hope to use this design as the base for other design work in new Presentations, web, and print work.

Industry/Entity Type

Engineering

Contact Information for Business Card

Our preferred color of blue is (RGB) 22/71/159 but can vary slightly from that color. Our content will be our Logo and full company name (Vantrell Forge Works, Inc.), company address, name, job title, phone number with extension, cell number, fax number, website, and email address on the cards.
We'd like the full company name next to the logo, but we are open to other interpretations of that layout.
Preferably, we would like the back side to be clean with just our logo, and the front to contain all of the contact information.

Colors
2f74b4
0355a3
85abd2

Requirements
Must have
• - Logo, company name, needed content - We are open to interpretation beyond that.
• - Standard size business card.
• - Horizontal orientation.
• - Enough space for lengthy names / job titles (for example, a job title could read "Directory of Human Resources" or "V.P. of Governmental Affairs"). We need this to look clean, whether the title be short (CEO) or long (as described above).

```html
<!DOCTYPE html>
<html lang="en">
<head>
<meta charset="utf-8">
<title>Vantrell Forge Works – Business Card</title>
<link rel="stylesheet" href="https://fonts.googleapis.com/css2?family=Roboto:ital,wght@0,400;0,500;0,700;0,900;1,900&family=Roboto+Condensed:wght@500&display=swap">
<style>
  :root {
    --brand-blue: #0f52a2;
    --brand-blue-deep: #0355a3;
    --ink: #1d1d1d;
    --ink-soft: #4a4a4a;
    --rule: #8a8a8a;
    --card-white: #f4f4f4;
    --stage: #e4e4e2;
    --white: #ffffff;
  }
  * { margin: 0; padding: 0; box-sizing: border-box; }
  html, body {
    width: 1200px; height: 960px; overflow: hidden;
    background: var(--stage);
    font-family: "Roboto", Arial, sans-serif;
  }
  .canvas { position: relative; width: 1200px; height: 960px; }

  .card {
    position: absolute;
    width: 600px; height: 338px;
    border-radius: 18px;
    overflow: hidden;
  }

  /* Front */
  .card-front {
    left: 302px; top: 128px;
    background: var(--card-white);
    border-bottom: 6px solid var(--brand-blue);
  }
  .front-wordmark {
    position: absolute; right: 42px; top: 50px;
    font-weight: 700; font-size: 50px; letter-spacing: 1px;
    color: var(--brand-blue);
    line-height: 1;
  }
  .holder-name {
    position: absolute; left: 32px; top: 192px;
    font-family: "Roboto Condensed", Arial, sans-serif;
    font-weight: 500; font-size: 26px;
    color: var(--brand-blue);
    line-height: 1;
  }
  .holder-title {
    position: absolute; left: 32px; top: 221px;
    font-size: 14px; color: var(--ink);
  }
  .divider {
    position: absolute; left: 32px; right: 44px; top: 247px;
    height: 1px; background: var(--rule);
  }
  .contact-list {
    position: absolute; left: 32px; top: 260px;
    list-style: none;
    font-size: 14px; color: var(--ink-soft);
  }
  .contact-list li {
    display: flex; align-items: center; gap: 8px;
    height: 18.5px;
  }
  .contact-list svg { width: 12px; height: 13px; fill: var(--brand-blue); }
  .address {
    position: absolute; right: 44px; top: 260px;
    font-style: normal; text-align: right;
    font-size: 14px; line-height: 18.5px; color: var(--ink-soft);
  }

  /* Back */
  .card-back {
    left: 298px; top: 488px;
    width: 602px; height: 344px;
    background: var(--brand-blue);
  }
  .back-lockup {
    position: absolute; left: 108px; top: 132px;
    display: flex; align-items: center; gap: 18px;
  }
  .back-wordmark {
    font-weight: 700; font-size: 52px; letter-spacing: 1px;
    color: var(--white); line-height: 1;
  }
  .company-name {
    font-weight: 900; font-style: italic;
    font-size: 18px; line-height: 21px;
    color: var(--white); text-transform: uppercase;
  }
  .company-name small { font-size: 9px; }
</style>
</head>
<body>
<main class="canvas">

  <section class="card card-front" aria-label="Business card front">
    <div class="front-wordmark">VANTRELL</div>

    <h1 class="holder-name">DORIAN KESSLER</h1>
    <p class="holder-title">V.P. of Governmental Affairs</p>
    <div class="divider"></div>

    <ul class="contact-list">
      <li>
        <svg viewBox="0 0 24 24" aria-hidden="true"><path d="M6.6 10.8a15.1 15.1 0 0 0 6.6 6.6l2.2-2.2c.3-.3.7-.4 1-.2 1.1.4 2.3.6 3.6.6.6 0 1 .4 1 1V20c0 .6-.4 1-1 1C10.6 21 3 13.4 3 4c0-.6.4-1 1-1h3.5c.6 0 1 .4 1 1 0 1.3.2 2.5.6 3.6.1.3 0 .7-.2 1z"/></svg>
        555 210 4471
      </li>
      <li>
        <svg viewBox="0 0 24 24" aria-hidden="true"><path d="M7 1h10a2 2 0 0 1 2 2v18a2 2 0 0 1-2 2H7a2 2 0 0 1-2-2V3a2 2 0 0 1 2-2zm0 3v14h10V4zm5 15.5a1 1 0 1 0 0 2 1 1 0 0 0 0-2z"/></svg>
        555 318 9026
      </li>
      <li>
        <svg viewBox="0 0 24 24" aria-hidden="true"><path d="M2 5h20v14H2zm2 2v.5l8 5 8-5V7zm0 2.8V17h16V9.8l-8 5z"/></svg>
        dorian@vantrell.com
      </li>
    </ul>

    <address class="address">
      412 Larkspur Way<br>
      Fairbanks, Alaska 99701<br>
      www.vantrell.com
    </address>
  </section>

  <section class="card card-back" aria-label="Business card back">
    <div class="back-lockup">
      <div class="back-wordmark">VANTRELL</div>
      <div class="company-name">Vantrell<br>Forge<br>Works <small>Inc</small></div>
    </div>
  </section>

</main>
</body>
</html>
```